Business Card Design

New business card design

Target Market(s)

Residential & Commercial Property Managers

Industry/Entity Type

Plumbing Services

Contact Information for Business Card

Name - Rowan Keddle, title - Director, Phone Number - 0431 286 517, email - rowan@tbk-plumbing.com.au, Company ABN - 73 215 904 386,

Font styles to use
Sans Serif

Colors
0054AA
0677BA
7BADD7
CADEEF
E8F1F8

```html
<!DOCTYPE html>
<html lang="en">
<head>
<meta charset="utf-8">
<title>TBK Plumbing Services – Business Card</title>
<link href="https://fonts.googleapis.com/css2?family=Montserrat:wght@400;500;700&display=swap" rel="stylesheet">
<style>
  :root {
    --stage: #232323;
    --card-dark: #1e2229;
    --card-light: #ffffff;
    --brand-blue: #2aa9e0;
    --bar-blue: #45b9ec;
    --ink: #1e2229;
    --ink-soft: #3a3f47;
  }
  * { box-sizing: border-box; margin: 0; padding: 0; }
  html, body {
    width: 1200px; height: 780px; overflow: hidden;
    background: var(--stage);
    font-family: "Montserrat", Arial, sans-serif;
  }
  .stage {
    width: 1200px; height: 780px;
    display: flex; align-items: center; justify-content: center; gap: 40px;
  }
  .card {
    position: relative;
    width: 540px; height: 310px;
    border-radius: 24px;
    border-bottom: 5px solid var(--brand-blue);
    border-left: 2px solid var(--brand-blue);
    overflow: hidden;
    box-shadow: 0 12px 30px rgba(0,0,0,.55);
  }
  .card--back { background: var(--card-dark); display: flex; align-items: center; justify-content: center; }
  .card--front { background: var(--card-light); color: var(--ink); }

  .brand { display: flex; align-items: center; gap: 12px; }
  .brand__dot { width: 14px; height: 14px; border-radius: 50%; background: var(--brand-blue); }
  .brand__name { font-weight: 500; letter-spacing: .02em; }
  .card--back .brand__dot { background: var(--ink-soft); width: 18px; height: 18px; }
  .card--back .brand__name { color: var(--ink-soft); font-size: 26px; }

  .card--front .brand { position: absolute; left: 38px; top: 48px; }
  .card--front .brand__name { font-size: 24px; color: var(--ink); }

  .person { position: absolute; left: 0; top: 168px; display: flex; }
  .person__bar { width: 14px; height: 52px; background: var(--bar-blue); margin-right: 24px; }
  .person__name { font-weight: 700; font-size: 21px; color: var(--brand-blue); line-height: 1.15; }
  .person__title { font-size: 15px; font-weight: 400; color: var(--ink); margin-top: 4px; }

  .contact { position: absolute; left: 38px; bottom: 30px; list-style: none; font-size: 14px; }
  .contact__item { display: flex; align-items: center; gap: 10px; margin-top: 8px; }
  .contact__icon { width: 16px; height: 16px; fill: var(--brand-blue); flex: none; }

  .abn { position: absolute; right: 30px; bottom: 33px; font-size: 13px; }
</style>
</head>
<body>
<main class="stage">
  <section class="card card--back" aria-label="Card back">
    <div class="brand">
      <span class="brand__dot"></span>
      <span class="brand__name">TBK Plumbing Services</span>
    </div>
  </section>

  <section class="card card--front" aria-label="Card front">
    <div class="brand">
      <span class="brand__name">TBK Plumbing Services</span>
      <span class="brand__dot"></span>
    </div>

    <div class="person">
      <span class="person__bar"></span>
      <div>
        <p class="person__name">Rowan Keddle</p>
        <p class="person__title">Director</p>
      </div>
    </div>

    <ul class="contact">
      <li class="contact__item">
        <svg class="contact__icon" viewBox="0 0 24 24" aria-hidden="true"><path d="M6.6 10.8a15.1 15.1 0 0 0 6.6 6.6l2.2-2.2a1 1 0 0 1 1-.25 11.4 11.4 0 0 0 3.6.57 1 1 0 0 1 1 1V20a1 1 0 0 1-1 1A17 17 0 0 1 3 4a1 1 0 0 1 1-1h3.5a1 1 0 0 1 1 1c0 1.25.2 2.45.57 3.57a1 1 0 0 1-.25 1z"/></svg>
        <span>0431 286 517</span>
      </li>
      <li class="contact__item">
        <svg class="contact__icon" viewBox="0 0 24 24" aria-hidden="true"><path d="M3 5h18a1 1 0 0 1 1 1v12a1 1 0 0 1-1 1H3a1 1 0 0 1-1-1V6a1 1 0 0 1 1-1zm1 2.2V17h16V7.2l-8 5.3z"/></svg>
        <span>rowan@tbk-plumbing.com.au</span>
      </li>
    </ul>

    <p class="abn">Company ABN - 73 215 904 386</p>
  </section>
</main>
</body>
</html>
```